Prime Global Casting Agency Needs creative business card design

We manage actors careers and book them liaising and promoting their profiles internationally through Casting Directors, Producers, Directors, Publicists etc. We need clearly visable contact details but with a design that reflects our status and creativity of TV, Feature Film industry. Our logo is attached and needs to relate and our website is www.brisklanestagefolk.com
No flame designs please but please incorporate logo colours.

Target Market(s)

Clients

Industry/Entity Type

Film Production

Contact Information for Business Card

Director Danielle Prowse
Suite F, Building 4, Wrenlow Studios Australia, Kelby Vale, Sydney, NSW 2048

Font styles to use
Sans Serif

Colors
ec1f27

Requirements
Nice to have
• Colours should relate to logo attached and type can relate again to type in the logo design.
Should not have
• No Flames designs and best to be not too obvious with the film designs eiither. Needs to be more creative and modern

```html
<!DOCTYPE html>
<html lang="en">
<head>
<meta charset="utf-8">
<title>Brisklane Stagefolk – Business Card</title>
<link href="https://fonts.googleapis.com/css2?family=Source+Sans+3:wght@400;600&display=swap" rel="stylesheet">
<style>
  :root {
    --stage: #1c1c1c;
    --card-white: #ffffff;
    --card-red: #e1232b;
    --brand-red: #c8202a;
    --accent-orange: #ee7623;
    --ink: #3a3a3a;
  }
  * { margin: 0; padding: 0; box-sizing: border-box; }
  html, body {
    width: 1200px; height: 900px; overflow: hidden;
    background: var(--stage);
    font-family: "Source Sans 3", sans-serif;
  }
  .card {
    position: absolute;
    top: 311px;
    width: 432px; height: 250px;
    border-radius: 12px;
  }
  .card--front { left: 155px; background: var(--card-white); }
  .card--back  { left: 629px; background: var(--card-red); }

  .brand-name {
    position: absolute;
    font-weight: 600;
    white-space: nowrap;
    letter-spacing: 0.5px;
  }
  .card--front .brand-name {
    left: 45px; top: 112px;
    font-size: 17px;
    color: var(--brand-red);
  }
  .card--back .brand-name {
    left: 84px; top: 96px;
    font-size: 36px;
    line-height: 1;
    color: var(--card-white);
  }
  .card--back .brand-name small {
    display: block;
    font-size: 36px;
    font-weight: 600;
  }

  .contact {
    position: absolute;
    left: 251px; top: 41px;
    color: var(--ink);
    font-size: 13.5px;
    line-height: 16px;
  }
  .contact__name {
    color: var(--accent-orange);
    font-weight: 600;
    font-size: 20px;
    line-height: 24px;
  }
  .contact__title { margin-bottom: 10px; }
  .contact__address { margin-bottom: 12px; }
  .contact__list { list-style: none; }
  .contact__list li {
    display: flex; align-items: center;
    height: 16.3px;
  }
  .contact__list svg {
    width: 9px; height: 9px;
    margin: 0 8px 0 2px;
    fill: var(--accent-orange);
    stroke: var(--accent-orange);
  }
</style>
</head>
<body>

<section class="card card--front" aria-label="Business card front">
  <div class="brand-name">BRISKLANE STAGEFOLK</div>

  <div class="contact">
    <div class="contact__name">Jonathan Smith</div>
    <div class="contact__title">Managing Director</div>
    <div class="contact__address">1234, Address Goes Here<br>Country Name, 123456</div>
    <ul class="contact__list">
      <li>
        <svg viewBox="0 0 10 10" aria-hidden="true"><rect x="2.5" y="0.5" width="5" height="9" rx="1" fill="none" stroke-width="1.2"/></svg>
        123-456-7890
      </li>
      <li>
        <svg viewBox="0 0 10 10" aria-hidden="true"><path d="M0 4 Q5 0 10 4 L8.5 5.5 L7 4.5 L3 4.5 L1.5 5.5 Z M2 6 H8 V9 H2 Z" stroke="none"/></svg>
        123-456-7890
      </li>
      <li>
        <svg viewBox="0 0 10 10" aria-hidden="true"><rect x="1" y="4" width="8" height="5.5" rx="0.8" stroke="none"/><rect x="3" y="0.5" width="4" height="4" fill="none" stroke-width="1"/></svg>
        123-456-7890
      </li>
      <li>
        <svg viewBox="0 0 10 10" aria-hidden="true"><rect x="0.5" y="2" width="9" height="6.5" stroke="none"/><path d="M0.5 2 L5 6 L9.5 2" fill="none" stroke="#fff" stroke-width="0.9"/></svg>
        info@youremail.com
      </li>
      <li>
        <svg viewBox="0 0 10 10" aria-hidden="true"><path d="M4 6 L6 4 M3.5 4.5 L2 6 A1.4 1.4 0 0 0 4 8 L5.5 6.5 M6.5 5.5 L8 4 A1.4 1.4 0 0 0 6 2 L4.5 3.5" fill="none" stroke-width="1.1"/></svg>
        www.yourweb.com
      </li>
    </ul>
  </div>
</section>

<section class="card card--back" aria-label="Business card back">
  <div class="brand-name">BRISKLANE<small>STAGEFOLK</small></div>
</section>

</body>
</html>
```